Awesome photographers card for an awesome new business

Double sided business card Black background and silver logo in middle on one side. Details on otherside. please keep it simple

Industry/Entity Type

Photographer

Contact Information for Business Card

Gerald Fenwick
0452817360
GeraldFenwickPhotography47@mailbox.test
www.GeraldFenwickPhotography.test.au
Instagram _Gerald_fenwick

Requirements
Must have
• My logo in Silver
• please use instagram logo instead of "Instagram"

```html
<!DOCTYPE html>
<html lang="en">
<head>
<meta charset="utf-8">
<title>Gerald Fenwick Photography – Business Card</title>
<link rel="stylesheet" href="https://fonts.googleapis.com/css2?family=Open+Sans:wght@400;600&display=swap">
<style>
  :root {
    --backdrop: #6b6b6b;
    --card-light: #f2f2f2;
    --card-dark: #2b2c2e;
    --ink: #2e2e2e;
    --ink-soft: #3a3a3a;
    --rule: #b9b9b9;
    --silver: #cfcfcf;
  }
  * { box-sizing: border-box; margin: 0; padding: 0; }
  html, body {
    width: 1200px; height: 900px; overflow: hidden;
    background: var(--backdrop);
    font-family: "Open Sans", Arial, sans-serif;
  }
  .canvas { position: relative; width: 1200px; height: 900px; }
  .card {
    position: absolute; top: 170px;
    width: 347px; height: 561px;
  }
  .card--front { left: 259px; background: var(--card-light); color: var(--ink); }
  .card--back { left: 631px; background: var(--card-dark); }

  .brand-mark {
    position: absolute; left: 50%; transform: translateX(-50%);
    display: flex; flex-direction: column; align-items: center; gap: 12px;
  }
  .card--front .brand-mark { top: 70px; }
  .card--back .brand-mark { top: 200px; }
  .brand-mark__dot {
    width: 46px; height: 46px; border-radius: 50%;
    border: 3px solid currentColor;
  }
  .brand-mark__name {
    font-size: 22px; font-weight: 400; letter-spacing: 3px;
    text-transform: uppercase; white-space: nowrap;
  }
  .card--front .brand-mark { color: var(--ink-soft); }
  .card--back .brand-mark { color: var(--silver); }

  .holder-name {
    position: absolute; top: 306px; width: 100%;
    text-align: center; font-size: 20px; font-weight: 600;
    color: var(--ink); letter-spacing: 0.2px;
  }
  .rule {
    position: absolute; left: 50%; transform: translateX(-50%);
    width: 175px; height: 1px;
    background: linear-gradient(90deg, transparent, var(--rule), transparent);
  }
  .rule--top { top: 351px; }
  .rule--bottom { top: 475px; }
  .contact-icons {
    position: absolute; top: 374px; width: 100%;
    display: flex; justify-content: center; gap: 3px;
  }
  .contact-list {
    position: absolute; top: 395px; width: 100%;
    text-align: center; font-size: 15px; line-height: 20.5px;
    color: var(--ink); list-style: none;
  }
  .social {
    position: absolute; top: 494px; width: 100%;
    display: flex; justify-content: center; align-items: center; gap: 6px;
    font-size: 15px; color: var(--ink);
  }
  .social__box {
    width: 16px; height: 16px; border-radius: 3px; background: var(--ink);
  }
</style>
</head>
<body>
<main class="canvas">
  <section class="card card--front" aria-label="Card front with contact details">
    <div class="brand-mark">
      <span class="brand-mark__dot"></span>
      <span class="brand-mark__name">Gerald Fenwick</span>
    </div>

    <h1 class="holder-name">GERALD FENWICK</h1>
    <div class="rule rule--top"></div>

    <div class="contact-icons" aria-hidden="true">
      <svg width="11" height="11" viewBox="0 0 12 12"><path d="M2.5 1h2l1 3-1.3 1a6.5 6.5 0 0 0 2.8 2.8l1-1.3 3 1v2c0 .6-.5 1-1 1A9.5 9.5 0 0 1 1.5 2c0-.5.4-1 1-1z" fill="#333"/></svg>
      <svg width="11" height="11" viewBox="0 0 12 12"><rect x="1" y="2.5" width="10" height="7" fill="#333"/><path d="M1 2.8l5 3.8 5-3.8" stroke="#f2f2f2" stroke-width="1" fill="none"/></svg>
      <svg width="11" height="11" viewBox="0 0 12 12"><circle cx="6" cy="6" r="5" fill="#333"/><path d="M1 6h10M6 1c-2.5 3-2.5 7 0 10M6 1c2.5 3 2.5 7 0 10" stroke="#f2f2f2" stroke-width=".8" fill="none"/></svg>
    </div>

    <ul class="contact-list">
      <li>0452817360</li>
      <li>GeraldFenwickPhotography47@mailbox.test</li>
      <li>www.GeraldFenwickPhotography.test.au</li>
    </ul>
    <div class="rule rule--bottom"></div>

    <div class="social">
      <span class="social__box" aria-hidden="true"></span>
      <span>_Gerald_fenwick</span>
    </div>
  </section>

  <section class="card card--back" aria-label="Card back with silver brand mark">
    <div class="brand-mark">
      <span class="brand-mark__dot"></span>
      <span class="brand-mark__name">Gerald Fenwick</span>
    </div>
  </section>
</main>
</body>
</html>
```